Bran-well Tide Gate Custom Brokers Limited

Name: Lorvina Hadcott
Title: Customs Broker
Address: Shop 9 Ferncliff Commercial Complex
207-209 Mulgrave Road
Kingston 8
Telephone: (876)
Email: tidegatewell@mailbrook.example

```html
<!DOCTYPE html>
<html lang="en">
<head>
<meta charset="utf-8">
<title>Bran-well Tide Gate Custom Brokers Limited – Business Cards</title>
<link rel="stylesheet" href="https://fonts.googleapis.com/css2?family=Poppins:wght@400;600;700&display=swap">
<style>
  :root {
    --navy: #0d2b52;
    --gold: #e8a90c;
    --grey: #9b9b9b;
    --card: #ffffff;
    --backdrop: #1c1c1e;
  }
  * { margin: 0; padding: 0; box-sizing: border-box; }
  html, body {
    width: 1200px; height: 1189px; overflow: hidden;
    background: var(--backdrop);
    font-family: "Poppins", sans-serif;
  }
  .canvas { position: relative; width: 1200px; height: 1189px; }
  .card {
    position: absolute; left: 150px;
    width: 900px; height: 514px;
    background: var(--card);
    border-radius: 36px;
    overflow: hidden;
  }
  .card--front { top: 50px; }
  .card--back { top: 620px; }

  .brand {
    display: flex; align-items: center; gap: 18px;
    color: var(--navy);
    font-weight: 700;
  }
  .brand__mark {
    flex: none; border-radius: 50%;
    background: var(--navy);
  }
  .brand__name {
    line-height: 1.2; text-transform: uppercase; letter-spacing: 0.02em;
    white-space: nowrap;
  }

  .card--front .brand {
    position: absolute; left: 50%; top: 50%;
    transform: translate(-50%, -50%);
  }
  .card--front .brand__mark { width: 72px; height: 72px; }
  .card--front .brand__name { font-size: 34px; }

  .card--back .brand { position: absolute; right: 60px; top: 64px; }
  .card--back .brand__mark { width: 50px; height: 50px; }
  .card--back .brand__name { font-size: 21px; }

  .contact { position: absolute; left: 70px; top: 62px; }
  .contact__name {
    color: var(--navy); font-weight: 700; font-size: 30px;
    text-transform: uppercase; letter-spacing: 0.01em; line-height: 1.1;
  }
  .contact__title { color: var(--gold); font-size: 22px; font-weight: 400; line-height: 1.4; }
  .contact__address {
    margin-top: 22px; color: var(--grey); font-size: 20px; line-height: 1.3;
    font-style: normal;
  }
  .contact__lines { margin-top: 18px; list-style: none; }
  .contact__line {
    display: flex; align-items: center; gap: 14px;
    color: var(--grey); font-size: 20px; line-height: 1.5;
  }
  .icon {
    width: 26px; height: 26px; border-radius: 50%;
    background: var(--gold);
    display: flex; align-items: center; justify-content: center;
    flex: none;
  }
  .waves { position: absolute; left: 0; top: 0; width: 900px; height: 514px; }
  .waves .navy { fill: var(--navy); }
  .waves .gold { fill: var(--gold); }
</style>
</head>
<body>
<main class="canvas">

  <section class="card card--front" aria-label="Card front">
    <div class="brand">
      <span class="brand__mark"></span>
      <span class="brand__name">Bran-well Tide Gate<br>Custom Brokers Limited</span>
    </div>
  </section>

  <section class="card card--back" aria-label="Card back">
    <svg class="waves" viewBox="0 0 900 514" aria-hidden="true">
      <path class="navy" d="M0 410 C300 405 600 350 900 270 L900 292 C600 372 300 428 0 434 Z"/>
      <path class="gold" d="M0 448 C300 444 600 386 900 310 L900 328 C600 406 300 466 0 470 Z"/>
      <path class="navy" d="M0 486 C300 482 600 428 900 350 L900 514 L0 514 Z"/>
    </svg>

    <div class="brand">
      <span class="brand__mark"></span>
      <span class="brand__name">Bran-well Tide Gate<br>Custom Brokers Limited</span>
    </div>

    <div class="contact">
      <h1 class="contact__name">Lorvina Hadcott</h1>
      <p class="contact__title">Customs Broker</p>
      <address class="contact__address">
        Shop 9 Ferncliff<br>
        Commercial Complex<br>
        207-209 Mulgrave Road<br>
        Kingston 8
      </address>
      <ul class="contact__lines">
        <li class="contact__line">
          <span class="icon">
            <svg width="14" height="14" viewBox="0 0 14 14" aria-hidden="true"><rect x="3" y="1" width="8" height="12" rx="1.5" fill="none" stroke="#fff" stroke-width="1.6"/></svg>
          </span>
          (876) 555 014 2290
        </li>
        <li class="contact__line">
          <span class="icon">
            <svg width="15" height="12" viewBox="0 0 15 12" aria-hidden="true"><rect x="1" y="1" width="13" height="10" fill="none" stroke="#fff" stroke-width="1.4"/><path d="M1 1 L7.5 7 L14 1" fill="none" stroke="#fff" stroke-width="1.4"/></svg>
          </span>
          tidegatewell@mailbrook.example
        </li>
      </ul>
    </div>
  </section>

</main>
</body>
</html>
```